Harbourline Electrical Solutions

On one side. LOGO (underneath:) Commercial Industrial Residential

- NAME & CONTACT DETAILS

Marcus T. Hollings
Project Manager

(Cell icon) (441) 555-0187
(Email icon) hlelectricalsolutions@mailvento.com
(Facebook & Instagram icons )@hlelectricalsolutions

Other side: LOGO - underneath ELECTRICAL CONSTRUCTION & MAINTENANCE . LED LIGHTING & AUTOMATION . LIFE SAFETY SYSTEMS (FIRE ALARM / SECURITY) . DATA & COMMUNICATION

```html
<!DOCTYPE html>
<html lang="en">
<head>
<meta charset="utf-8">
<title>Harbourline Electrical Solutions – Business Card</title>
<link href="https://fonts.googleapis.com/css2?family=Montserrat:wght@400;500;600;700&display=swap" rel="stylesheet">
<style>
  :root {
    --bg: #d9d9d9;
    --slate: #5b5c5e;
    --slate-dark: #3f4042;
    --slate-text: #2c2d2f;
    --teal: #1d6b80;
    --teal-deep: #145a6c;
    --white: #ffffff;
    --ink: #2f3336;
    --swoosh: #4a4c4f;
  }
  * { box-sizing: border-box; margin: 0; padding: 0; }
  html, body { width: 1200px; height: 960px; overflow: hidden; }
  body {
    background: var(--bg);
    font-family: "Montserrat", sans-serif;
    position: relative;
  }
  .card {
    position: absolute;
    left: 250px;
    width: 700px;
    height: 400px;
    border-radius: 22px;
    overflow: hidden;
    box-shadow: 0 8px 24px rgba(0,0,0,.18);
  }
  /* Back side */
  .card-back {
    top: 50px;
    background: linear-gradient(135deg, var(--slate) 0%, var(--slate-dark) 100%);
    display: flex;
    flex-direction: column;
    align-items: center;
    justify-content: center;
    gap: 34px;
  }
  .back-wordmark {
    display: flex;
    align-items: center;
    gap: 14px;
    font-weight: 600;
    font-size: 30px;
    letter-spacing: 3px;
    color: var(--slate-text);
    text-transform: uppercase;
    line-height: 1.15;
  }
  .back-wordmark .mark-square {
    width: 22px; height: 22px; background: var(--slate-text);
  }
  .services {
    text-align: center;
    font-size: 15px;
    font-weight: 500;
    color: var(--slate-text);
    line-height: 1.6;
  }
  /* Front side */
  .card-front {
    top: 500px;
    background: var(--white);
  }
  .card-front svg.wave {
    position: absolute; inset: 0;
  }
  .front-brand {
    position: absolute;
    left: 44px;
    top: 80px;
  }
  .front-wordmark {
    display: flex;
    align-items: center;
    gap: 10px;
    font-weight: 600;
    font-size: 19px;
    letter-spacing: 1.5px;
    color: var(--teal);
    text-transform: uppercase;
    line-height: 1.2;
  }
  .front-wordmark .mark-square {
    width: 15px; height: 15px; background: var(--teal);
  }
  .sectors {
    margin-top: 14px;
    font-size: 13px;
    font-weight: 500;
    letter-spacing: .4px;
    color: var(--ink);
    text-transform: uppercase;
  }
  .contact {
    position: absolute;
    right: 34px;
    top: 180px;
    text-align: right;
    color: var(--white);
  }
  .person-name {
    font-size: 20px;
    font-weight: 700;
    letter-spacing: 1px;
    text-transform: uppercase;
  }
  .person-role {
    font-size: 13px;
    font-weight: 500;
    margin-bottom: 12px;
  }
  .contact-row {
    display: flex;
    justify-content: flex-end;
    align-items: center;
    gap: 9px;
    font-size: 13px;
    line-height: 1.75;
  }
  .contact-row svg { width: 13px; height: 13px; flex: none; }
</style>
</head>
<body>

<section class="card card-back" aria-label="Card back">
  <div class="back-wordmark">
    <span class="mark-square"></span>
    <span>Harbourline<br>Electrical Solutions</span>
  </div>
  <p class="services">
    Electrical Construction &amp; Maintenance • LED Lighting &amp; Automation<br>
    Life Safety Systems (Fire Alarm / Security) • Data &amp; Communication
  </p>
</section>

<section class="card card-front" aria-label="Card front">
  <svg class="wave" viewBox="0 0 700 400" width="700" height="400" aria-hidden="true">
    <defs>
      <linearGradient id="tealFill" x1="0" y1="0" x2="1" y2="1">
        <stop offset="0" stop-color="#1f7186"/>
        <stop offset="1" stop-color="#145a6c"/>
      </linearGradient>
    </defs>
    <path d="M700 0 L560 0 C460 0 450 130 395 220 C340 300 210 325 0 330 L0 400 L700 400 Z" fill="url(#tealFill)"/>
    <path d="M372 190 C355 272 250 312 0 318 L0 324 C240 320 357 285 372 190 Z" fill="var(--swoosh)"/>
  </svg>

  <div class="front-brand">
    <div class="front-wordmark">
      <span class="mark-square"></span>
      <span>Harbourline<br>Electrical Solutions</span>
    </div>
    <p class="sectors">Commercial • Industrial • Residential</p>
  </div>

  <div class="contact">
    <p class="person-name">Marcus T. Hollings</p>
    <p class="person-role">Project Manager</p>
    <p class="contact-row">(441) 555-0187
      <svg viewBox="0 0 13 13"><rect x="3" y="0.5" width="7" height="12" rx="1.5" fill="none" stroke="#fff" stroke-width="1.3"/><circle cx="6.5" cy="10.3" r=".8" fill="#fff"/></svg>
    </p>
    <p class="contact-row">hlelectricalsolutions@mailvento.com
      <svg viewBox="0 0 13 13"><rect x="0.5" y="2.5" width="12" height="8" fill="none" stroke="#fff" stroke-width="1.2"/><path d="M0.5 2.5 L6.5 7 L12.5 2.5" fill="none" stroke="#fff" stroke-width="1.2"/></svg>
    </p>
    <p class="contact-row">@hlelectricalsolutions
      <svg viewBox="0 0 13 13"><circle cx="6.5" cy="6.5" r="6" fill="#fff"/></svg>
    </p>
    <p class="contact-row">@hlelectricalsolutions
      <svg viewBox="0 0 13 13"><circle cx="6.5" cy="6.5" r="6" fill="#fff"/></svg>
    </p>
  </div>
</section>

</body>
</html>
```